Brightmill Data Works

Our company is about IT hardwares and IT solutions. IT hardware such as PC, RAMS, storage and servers. IT solutions such as project management, BA. We are also selling new technology too.

Target Market(s)

Consumer, Small to Medium Business, Corporate

Requirements
Must have
• The business card must have the following:
• Name:
• Title:
• Contact Number:
• Email address:
• Website:
• Color: Must match the logo color upgrade

```html
<!DOCTYPE html>
<html lang="en">
<head>
<meta charset="utf-8">
<title>Brightmill Data Works — Business Card</title>
<link rel="stylesheet" href="https://fonts.googleapis.com/css2?family=Roboto:wght@300;400;500&display=swap">
<style>
  :root {
    --bg: #2a2a2a;
    --card-white: #f4f4f4;
    --orange-light: #c9702e;
    --orange-dark: #b5552a;
    --ink: #3d3e42;
    --white: #ffffff;
    --icon-ink: #c0652c;
  }
  * { box-sizing: border-box; margin: 0; padding: 0; }
  html, body {
    width: 1200px; height: 923px; overflow: hidden;
    background: var(--bg);
    font-family: "Roboto", Arial, sans-serif;
  }
  .canvas {
    position: relative; width: 1200px; height: 923px;
    display: flex; align-items: center; justify-content: center; gap: 60px;
  }
  .card {
    position: relative; width: 525px; height: 300px;
    border-radius: 4px; overflow: hidden;
    box-shadow: 0 10px 30px rgba(0,0,0,.45);
  }
  .card-back {
    background: var(--card-white);
    display: flex; align-items: center; justify-content: center;
  }
  .card-front {
    background: linear-gradient(135deg, var(--orange-light) 0%, var(--orange-dark) 65%, var(--orange-light) 100%);
  }
  .card-curves { position: absolute; inset: 0; width: 100%; height: 100%; }
  .brand {
    display: flex; align-items: center; gap: 12px;
    font-weight: 500; font-size: 26px; letter-spacing: 1px;
    text-transform: uppercase; color: var(--ink);
  }
  .brand-square { width: 22px; height: 22px; background: var(--orange-light); }
  .card-front .brand {
    position: absolute; top: 62px; left: 0; right: 0; justify-content: center;
  }
  .card-front .brand-square { background: var(--white); }
  .holder {
    position: absolute; left: 36px; bottom: 42px; color: var(--white);
    text-transform: uppercase; line-height: 1.15;
  }
  .holder-name { font-size: 22px; font-weight: 400; }
  .holder-title { font-size: 17px; font-weight: 400; }
  .contacts {
    position: absolute; right: 30px; top: 140px; list-style: none;
    color: var(--white); font-weight: 300; font-size: 15px; letter-spacing: .5px;
  }
  .contacts li {
    display: flex; align-items: center; justify-content: flex-end; gap: 10px;
    margin-bottom: 6px;
  }
  .contact-icon {
    width: 17px; height: 17px; background: var(--white); border-radius: 2px;
    display: flex; align-items: center; justify-content: center;
  }
  .contact-icon svg { width: 11px; height: 11px; }
</style>
</head>
<body>
<main class="canvas">
  <section class="card card-back">
    <div class="brand"><span class="brand-square"></span>Brightmill Data Works</div>
  </section>

  <section class="card card-front">
    <svg class="card-curves" viewBox="0 0 525 300" preserveAspectRatio="none" aria-hidden="true">
      <path d="M330 0 C 420 90, 470 190, 525 230 L525 0 Z" fill="rgba(255,255,255,.06)"/>
      <path d="M400 0 C 460 80, 500 150, 525 170 L525 0 Z" fill="rgba(255,255,255,.06)"/>
    </svg>
    <div class="brand"><span class="brand-square"></span>Brightmill Data Works</div>
    <ul class="contacts">
      <li>+1-555-014-2870
        <span class="contact-icon"><svg viewBox="0 0 12 12"><path d="M2.5 1 L4.5 1 L5.2 3.6 L4 4.6 C4.6 6 6 7.4 7.4 8 L8.4 6.8 L11 7.5 L11 9.5 C11 10.3 10.3 11 9.5 11 C5 11 1 7 1 2.5 C1 1.7 1.7 1 2.5 1 Z" fill="var(--icon-ink)"/></svg></span>
      </li>
      <li>dana@brightmilldata.com
        <span class="contact-icon"><svg viewBox="0 0 12 12"><rect x="1" y="2.5" width="10" height="7" fill="none" stroke="var(--icon-ink)" stroke-width="1.2"/><path d="M1 2.5 L6 6.5 L11 2.5" fill="none" stroke="var(--icon-ink)" stroke-width="1.2"/></svg></span>
      </li>
      <li>www.brightmilldata.com
        <span class="contact-icon"><svg viewBox="0 0 12 12"><circle cx="6" cy="6" r="4.6" fill="none" stroke="var(--icon-ink)" stroke-width="1.1"/><ellipse cx="6" cy="6" rx="2" ry="4.6" fill="none" stroke="var(--icon-ink)" stroke-width="1"/><path d="M1.4 6 H10.6" stroke="var(--icon-ink)" stroke-width="1"/></svg></span>
      </li>
    </ul>
    <div class="holder">
      <p class="holder-name">Dana Whitlow</p>
      <p class="holder-title">Manager</p>
    </div>
  </section>
</main>
</body>
</html>
```